Make a medical leaflet for my patients undergoing ankle blocks

I have a very boring text only leaflet I would like to turn into a professional appealing medical leaflet to give to my patients. I would like to get this onto two pages of a4 if possible and its intended for electronic distribution mainly.
This will be for patients so it must be professional.
It must also contain a copyright logo on it and my name near the start (Dr Paul Venning) so my colleagues can't use it easily.
Target Market(s)
Patients undergoing surgery
Industry/Entity Type
Medical
Font styles to use
Other font styles liked:
- no idea, you tell me
Requirements
Must have
- the information contained on the attachment
- look professional
- a copyright on it
Nice to have
- the harbour infirmary logo
Should not have
- Any spelling, grammatical or linguistic errors
- Any font less than size 12

```html
<!DOCTYPE html>
<html lang="en">
<head>
<meta charset="utf-8">
<title>Undergoing Ankle Blocks – Patient Leaflet</title>
<link href="https://fonts.googleapis.com/css2?family=Montserrat:wght@600;700&family=Raleway:wght@400;500;600&display=swap" rel="stylesheet">
<style>
:root{
  --blue:#2468b0;
  --navy:#232c5a;
  --teal:#2fa9b5;
  --ink:#3a3a3a;
  --muted:#7a7a7a;
  --paper:#ffffff;
  --backdrop:#b3b3b3;
}
*{box-sizing:border-box;margin:0;padding:0}
html,body{width:1200px;height:888px;overflow:hidden}
body{background:var(--backdrop);font-family:"Raleway",sans-serif;color:var(--ink);position:relative}
.page{position:absolute;top:48px;width:560px;height:792px;background:var(--paper);overflow:hidden}
.page--front{left:30px}
.page--back{left:610px}
.page__band{position:absolute;left:0;right:0;bottom:0;height:7px;background:var(--blue)}
.abs{position:absolute}
p{font-size:8.4px;line-height:1.3}

/* brand */
.brand__name{font-size:22px;font-weight:500;color:var(--navy);letter-spacing:.2px}
.brand__rule{height:1.5px;background:var(--navy);margin:3px 0 5px}
.brand__group{font-size:12px;font-weight:500;color:var(--teal);text-align:center}

.clinic-box{left:408px;top:0;width:132px;height:122px;background:var(--blue);display:flex;align-items:center;justify-content:center;text-align:center}
.clinic-box__name{font-size:15px;font-weight:500;line-height:1.3;color:#fff}

.name-band{left:0;top:95px;width:296px;height:26px}
.name-band__text{left:62px;top:101px;font-family:"Montserrat",sans-serif;font-weight:600;font-size:14px;color:#fff}

.photo{left:0;top:121px;width:262px;height:270px;background:linear-gradient(90deg,#b9cde0 0%,#d6c7d4 45%,#e8dde6 70%,rgba(255,255,255,0) 100%)}
.photo::after{content:"";position:absolute;left:0;right:0;bottom:0;height:90px;background:linear-gradient(rgba(255,255,255,0),#fff)}

.title{left:254px;top:141px;font-family:"Montserrat",sans-serif;font-weight:700;font-size:18.5px;color:var(--blue)}
.intro{left:254px;top:173px;width:286px}
.intro p{text-align:justify;margin-bottom:4px}

/* pill headings */
.pill{position:absolute;background:var(--blue);color:#fff;font-family:"Montserrat",sans-serif;font-weight:700;font-size:11.5px;padding:4px 13px;border-radius:12px;white-space:nowrap}
.hline{position:absolute;height:1.3px;background:var(--blue)}

.benefits{left:32px;top:386px;width:490px;height:98px;border:1.3px solid var(--blue);border-radius:12px}
.benefits__list{list-style:none;position:absolute;left:32px;top:402px;width:490px;text-align:center}
.benefits__list li{font-size:8.4px;line-height:16.4px}
.tick{display:inline-block;width:10px;height:10px;vertical-align:-1.5px;margin-right:6px}

.risks-lead{left:0;width:560px;top:536px;text-align:center}
.risk-table{left:19px;top:552px;width:521px;border-collapse:collapse}
.risk-table td{border:1px solid #b9b9b9;vertical-align:top;font-size:8.2px;line-height:1.3;padding:5px 10px}
.risk-table .risk-table__label{width:171px;font-family:"Montserrat",sans-serif;font-weight:700;font-size:9.5px;color:var(--blue)}
.risk-table ul{list-style:none}
.closing-note{left:30px;top:739px;width:500px;text-align:center}

.copyright{left:0;width:560px;top:771px;text-align:center;font-size:7.5px;color:var(--muted)}

/* back page */
.section-sub{position:absolute;left:0;width:560px;text-align:center;font-family:"Montserrat",sans-serif;font-weight:700;font-size:9.5px;color:var(--blue)}
.centered{position:absolute;left:26px;width:508px;text-align:center}
.ankle-photo{left:15px;top:293px;width:205px;height:222px;background:radial-gradient(ellipse at 55% 60%,#8a8f99 0%,#b8bcc3 45%,#e9ebee 80%,#ffffff 100%)}
.after-text{left:222px;top:287px;width:318px}
.after-text p{text-align:justify;margin-bottom:6px}
.alt-box{left:34px;top:548px;width:488px;height:72px;border:1.3px solid var(--blue);border-radius:12px}
.questions{left:40px;top:628px;width:480px;text-align:center;font-family:"Montserrat",sans-serif;font-weight:600;font-size:10.3px;line-height:1.4;color:var(--blue)}
.foot-brand{left:18px;top:700px;width:212px}
.foot-divider{left:290px;top:712px;width:1px;height:46px;background:#c8c8c8}
.foot-name{left:370px;top:721px;font-family:"Montserrat",sans-serif;font-weight:700;font-size:17.5px;color:var(--blue)}
</style>
</head>
<body>

<!-- Page 1 -->
<section class="page page--front">
  <div class="abs" style="left:20px;top:14px;width:250px">
    <div class="brand__name">Riverside Quay Hospital</div>
    <div class="brand__rule"></div>
    <div class="brand__group">part of Meridian Health UK</div>
  </div>

  <div class="abs clinic-box">
    <div class="clinic-box__name">The Harbour<br>Infirmary</div>
  </div>

  <svg class="abs name-band" viewBox="0 0 296 26" aria-hidden="true"><polygon points="0,0 286,0 296,26 0,26" fill="var(--blue)"/></svg>
  <div class="abs name-band__text">DR PAUL VENNING</div>

  <div class="abs photo" role="img" aria-label="Photograph of a nurse kneeling beside a smiling patient in a wheelchair"></div>

  <h1 class="abs title">UNDERGOING ANKLE BLOCKS</h1>
  <div class="abs intro">
    <p>You are scheduled to have surgery on your foot. It is my normal practice to offer and perform (with your consent) an ankle block. This is an optional injection of numbing liquid to the nerves which supply your foot. The ankle block can be performed when you are awake, sedated or under general anaesthesia.</p>
    <p>The ankle block can be combined with a general anaesthetic and with sedation. It can also be used to allow surgery to be performed with you wide awake in certain cases.</p>
    <p>Having or not having an ankle block does not change the pre operative fasting guidelines you have been given.</p>
    <p>There is a fee for performing an ankle block. Please consult my initial introductory email and terms of business for details</p>
  </div>

  <div class="abs benefits"></div>
  <div class="pill" style="left:190px;top:375px">WHAT ARE THE BENEFITS</div>
  <ul class="benefits__list">
    <li><svg class="tick" viewBox="0 0 10 10"><circle cx="5" cy="5" r="4" fill="none" stroke="var(--blue)" stroke-width="1"/><path d="M2.6 5.2l1.7 1.6L8.6 1.8" fill="none" stroke="var(--blue)" stroke-width="1.3"/></svg>Excellent pain relief - usually 10 - 14 hours (and rarely 24 - 48 hours)</li>
    <li><svg class="tick" viewBox="0 0 10 10"><circle cx="5" cy="5" r="4" fill="none" stroke="var(--blue)" stroke-width="1"/><path d="M2.6 5.2l1.7 1.6L8.6 1.8" fill="none" stroke="var(--blue)" stroke-width="1.3"/></svg>Avoiding traditional painkillers which resulting in less post operative nausea and vomiting</li>
    <li><svg class="tick" viewBox="0 0 10 10"><circle cx="5" cy="5" r="4" fill="none" stroke="var(--blue)" stroke-width="1"/><path d="M2.6 5.2l1.7 1.6L8.6 1.8" fill="none" stroke="var(--blue)" stroke-width="1.3"/></svg>The option to avoid a general anaesthetic (if you wish)</li>
    <li><svg class="tick" viewBox="0 0 10 10"><circle cx="5" cy="5" r="4" fill="none" stroke="var(--blue)" stroke-width="1"/><path d="M2.6 5.2l1.7 1.6L8.6 1.8" fill="none" stroke="var(--blue)" stroke-width="1.3"/></svg>A faster recovery from the general anaesthetic</li>
    <li><svg class="tick" viewBox="0 0 10 10"><circle cx="5" cy="5" r="4" fill="none" stroke="var(--blue)" stroke-width="1"/><path d="M2.6 5.2l1.7 1.6L8.6 1.8" fill="none" stroke="var(--blue)" stroke-width="1.3"/></svg>Certain surgery requires an overnight stay in hospital without an ankle block</li>
  </ul>

  <div class="hline" style="left:190px;top:525px;width:306px"></div>
  <div class="pill" style="left:191px;top:514px">WHAT ARE THE RISKS?</div>
  <p class="abs risks-lead">As with all injections, there is the risk of bruising, bleeding and infection.</p>

  <table class="abs risk-table">
    <tr>
      <td class="risk-table__label">NERVE DAMAGE</td>
      <td>Occurs 1 in 5000 nerve blocks.<br>Creates an area of numbness or weakness/paralysis in some / all the foot.<br>Majority of nerve injuries will heal themselves within a year<br>There is no treatment to fix it<br>If the block has not worn off after 72 hours please let me know.</td>
    </tr>
    <tr>
      <td class="risk-table__label">FAILURE</td>
      <td>The success rate with ankle blocks is 98 - 99%<br>Some blocks will fail, partially or totally.<br>If total failure, I will discuss repeating the block with your consent.</td>
    </tr>
    <tr>
      <td class="risk-table__label">PAIN DURING OPERATION</td>
      <td>If you choose to have wide awake surgery or surgery under sedation<br>The surgery will stop and I will discuss three options with you
        <ul><li>- &nbsp;more numbing liquid to be injected by the surgeon</li><li>- &nbsp;more sedation / painkiller</li><li>- &nbsp;having a general anaesthetic</li></ul></td>
    </tr>
  </table>
  <p class="abs closing-note">If you decide to undergo surgery awake or sedated, there is a risk you will need to have a general anaesthetic if you feel pain. This is why the starvation instructions of awake surgery and general anaesthesia are the same.</p>

  <p class="abs copyright">© Dr Paul Venning. All rights reserved.</p>
  <div class="page__band"></div>
</section>

<!-- Page 2 -->
<section class="page page--back">
  <div class="hline" style="left:147px;top:31px;width:266px"></div>
  <div class="pill" style="left:208px;top:20px">HOW IS IT DONE</div>

  <div class="section-sub" style="top:60px">IF YOU CHOOSE AWAKE SURGERY OR SURGERY WITH SEDATION -</div>
  <p class="centered" style="top:77px">Numbing liquid is injected around the nerves which supply your foot. The ankle block takes 5 - 10 minutes to perform and requires 4 - 5 injections. Approximately 10 - 20 minutes to make your foot numb to pain. I will check the ankle block is working before we start surgery using cold spray. Sensations of touch, pressure, vibration and movement will still be felt. I will use a screen so you can't see the surgery (unless you would like to see). Some patients bring headphones to block out the noise of the operation.</p>

  <div class="section-sub" style="top:166px">IF YOU CHOOSE A GENERAL ANAESTHETIC</div>
  <p class="centered" style="top:186px">I will perform the ankle block after I start the general anaesthetic. You should wake up from your surgery with a comfortable and numb foot/feet. If you wake in pain, we can repeat the ankle block or provide traditional painkillers</p>
  <p class="centered" style="top:228px">Whatever you choose, there will be a cannula placed in your hand and heart and oxygen monitoring throughout.</p>

  <div class="hline" style="left:300px;top:265px;width:240px"></div>
  <div class="pill" style="left:224px;top:254px">AFTER SURGERY</div>

  <div class="abs ankle-photo" role="img" aria-label="Photograph of a foot wearing a dark elastic ankle support"></div>
  <div class="abs after-text">
    <p>You will go to the recovery area and then onto the ward when you are ready. It will be difficult to walk while the block is working so physiotherapists will help you first walk. If you need crutches they will teach you how to use them.</p>
    <p>Your foot will be numb and so you will not feel where your foot is in relation to nearby objects. As a result, it is easy to knock your foot. Please take extra care while your foot is still numb.</p>
    <p>As the block wears off, the foot may feel slightly painful, tingly or hot. At this point you should take your painkillers I have prescribed. Depending on your medical history you will have up to three painkillers. I would suggest to start with all three. You will also have an anti - sickness prescribed if one of the painkillers (typically codeine or morphine) makes you feel sick.</p>
    <p>Occasionally (1 - 2%), pain when the block wears off will be severe. In this case contact your surgeon's secretary. We can use stronger pain medication, but there will be charge in writing and getting the private prescription to you (please see my terms of business) via courier.</p>
  </div>

  <div class="abs alt-box"></div>
  <div class="pill" style="left:218px;top:537px">THE ALTERNATIVE</div>
  <p class="centered" style="top:566px;line-height:1.45">If you do not have an ankle block your surgery can still proceed.<br>Post operative pain can be managed with traditional painkillers.<br>However, you are more likely to need an overnight stay or feel sick after the anaesthetic.</p>

  <div class="abs questions">If you have any further questions about an ankle block I will see you the day of your surgery. Alternatively, you can request the following optional services (as mentioned in my terms of business).</div>

  <div class="abs foot-brand">
    <div class="brand__name" style="font-size:18.5px">Riverside Quay Hospital</div>
    <div class="brand__rule"></div>
    <div class="brand__group" style="font-size:10.5px">part of Meridian Health UK</div>
  </div>
  <div class="abs foot-divider"></div>
  <div class="abs foot-name">DR PAUL VENNING</div>

  <p class="abs copyright">© Dr Paul Venning. All rights reserved.</p>
  <div class="page__band"></div>
</section>

</body>
</html>
```